Tree Pruning Website

We need a website for a tree Arborist, pruning company called Maple Crest Canopy Works. We look after all types of trees, knock down trees and prune trees. Our target market is from domestic clients to government clients and everything in between.

We would like to see the use of our main colours which are orange and green

We are not looking forward in seeing a template that we have seen before but a unique template. We have designed 5 templates ourselves and we wish for the design community to take our designs to the next level.

We have also designed a template for things that **we are not** looking for (Version 4)

To make it fair for everyone, we are also not giving out any participation payments as we have had. One winner will take all of the payment!!!

I Have attached a image of the designs and a image of a tree.

We are just looking at the PSD file been developed. We have our own team who can slice the image up into a HTML format.

Target Market(s)

Everyone who needs to cut down a tree

Industry/Entity Type

Government

Requirements
Must have
• Logo on front page
A List of our services
jQuery slider on page
Phone Number on every page

```html
<!DOCTYPE html>
<html lang="en">
<head>
<meta charset="utf-8">
<title>Maple Crest Canopy Works</title>
<link rel="stylesheet" href="https://fonts.googleapis.com/css2?family=Oswald:wght@400;500&family=Lato:wght@400;700&display=swap">
<style>
:root{
  --forest-dark:#1f2a14;
  --forest-mid:#3e5a24;
  --forest-light:#6f8f3c;
  --plank:#c9b66e;
  --plank-dark:#8d7a3c;
  --frame:#b98a5a;
  --cream:#efe8d3;
  --green:#3f6a0e;
  --green-bright:#8ab832;
  --olive:#5d6a22;
  --card-green:#3b4426;
  --card-orange:#7a3d07;
  --ink:#2a2a2a;
  --nav-top:#4a4a4a;
  --nav-bottom:#1e1e1e;
  --footer:#151515;
  --footer-text:#9a9a9a;
}
*{margin:0;padding:0;box-sizing:border-box}
html,body{width:1063px;height:1200px;overflow:hidden}
body{position:relative;background:var(--cream);font-family:"Lato",sans-serif;color:var(--ink)}
.abs{position:absolute}
.hero-backdrop{left:0;top:0;width:1063px;height:442px;background:radial-gradient(ellipse at 20% 60%,var(--forest-light),transparent 60%),radial-gradient(ellipse at 85% 40%,#5c7d32,transparent 55%),linear-gradient(180deg,#2c3a1c,var(--forest-mid) 60%,#2a3818)}
.logo-plank{left:166px;top:48px;width:284px;height:94px;background:linear-gradient(180deg,#d8c77f,var(--plank) 60%,#b6a25a);transform:rotate(-1.5deg);box-shadow:0 3px 6px rgba(0,0,0,.45)}
.logo-mark{left:18px;top:24px;width:42px;height:42px;border-radius:50%;background:var(--green-bright)}
.logo-name{left:90px;top:14px;font-family:"Oswald",sans-serif;font-weight:500;font-size:30px;color:#3a4a12;letter-spacing:1px}
.logo-tag{left:90px;top:60px;font-family:"Oswald",sans-serif;font-weight:500;font-size:14px;color:#3a4a12}
.phone{left:710px;top:68px;display:flex;align-items:center;gap:8px}
.phone-number{font-family:"Oswald",sans-serif;font-size:24px;color:#fff}
.slider-frame{left:159px;top:142px;width:745px;height:300px;background:var(--frame);box-shadow:0 0 8px rgba(0,0,0,.5)}
.slide-photo{left:9px;top:8px;width:728px;height:286px;background:linear-gradient(160deg,#7c95b8 0%,#dcd8cc 35%,#5e7a3a 60%,#e9e2d2 80%,#486a2f 100%)}
.slide-caption{left:168px;top:304px;width:464px;height:80px;background:rgba(30,30,30,.82)}
.caption-title{left:17px;top:14px;font-family:"Oswald",sans-serif;font-size:21px;color:var(--green-bright)}
.caption-text{left:19px;top:48px;font-family:"Oswald",sans-serif;font-size:12.5px;color:#fff}
.slide-dots{left:842px;top:416px;display:flex;gap:3px}
.slide-dots span{width:9px;height:9px;background:rgba(255,255,255,.5)}
.slide-dots span:first-child{background:#fff}
.main-nav{left:0;top:442px;width:1063px;height:56px;background:linear-gradient(180deg,var(--nav-top),var(--nav-bottom));border-bottom:1px solid #000}
.nav-item{top:0;height:56px;padding:11px 0 0 14px;color:#fff}
.nav-item.active{background:linear-gradient(180deg,#6b7a2a,var(--olive))}
.nav-title{font-family:"Oswald",sans-serif;font-size:16px;display:block}
.nav-sub{font-size:8.5px;display:block;margin-top:2px}
.welcome-title{left:161px;top:530px;font-family:"Oswald",sans-serif;font-size:25px;color:var(--green)}
.welcome-tag{left:163px;top:562px;font-family:"Oswald",sans-serif;font-size:15px;color:#222}
.welcome-divider{left:368px;top:528px;width:1px;height:54px;background:#bfb59a}
.welcome-text{left:390px;top:527px;width:514px;font-size:8.8px;line-height:13.6px}
.rule{left:159px;width:745px;height:1px;background:#c7bea5}
.card{top:628px;width:174px;height:162px;border-radius:3px;background:var(--card-green);color:#fff;text-align:center}
.card.highlight{background:var(--card-orange)}
.card h3{font-family:"Oswald",sans-serif;font-weight:400;font-size:19px;margin-top:12px}
.card svg{display:block;margin:8px auto 0}
.card p{font-size:8.2px;line-height:13.6px;font-weight:700;padding:0 14px;margin-top:6px}
.section-title{top:836px;font-family:"Oswald",sans-serif;font-size:25px;color:var(--green)}
.services-list{left:159px;top:869px;width:199px;list-style:none}
.services-list li{height:30.4px;border-bottom:1px solid #c7bea5;font-size:10.5px;display:flex;align-items:center;padding-left:18px;position:relative}
.services-list li:last-child{border-bottom:none}
.services-list li::before{content:"";position:absolute;left:4px;width:9px;height:9px;border-radius:50%;background:var(--green-bright)}
.carousel-arrow{top:847px;width:14px;height:14px;border-radius:50%;background:var(--green-bright)}
.thumb{top:877px;width:156px;height:100px;border:3px solid #e0d7bd}
.thumb-overlay{left:0;top:0;width:100%;height:100%;text-align:center;color:#fff;font-size:8px;font-weight:700;padding-top:20px;line-height:13.6px}
.works-text{left:390px;top:991px;width:514px;font-size:8.8px;line-height:13.6px}
.treeline{left:0;top:1030px;width:1063px;height:90px;background:linear-gradient(180deg,rgba(21,21,21,0) 0%,rgba(21,21,21,.6) 50%,var(--footer) 100%)}
.site-footer{left:0;top:1120px;width:1063px;height:80px;background:var(--footer)}
.footer-links{left:161px;top:32px;display:flex;font-size:8.3px;color:var(--footer-text)}
.footer-links span{padding:0 16px;border-left:1px solid #666}
.footer-links span:first-child{padding-left:0;border-left:none}
.copyright{left:161px;top:49px;font-size:8px;color:var(--footer-text)}
.copyright b{color:var(--green-bright);font-weight:400}
.social-label{left:740px;top:32px;width:83px;text-align:right;font-size:8px;line-height:13.5px;color:var(--footer-text)}
.social{top:34px;width:19px;height:19px;border-radius:3px;background:#5b8ab0}
</style>
</head>
<body>

<header>
  <div class="abs hero-backdrop" role="img" aria-label="Blurred forest photograph background"></div>
  <div class="abs logo-plank">
    <div class="abs logo-mark"></div>
    <div class="abs logo-name">MCCW</div>
    <div class="abs logo-tag">Maple Crest Canopy Works</div>
  </div>
  <div class="abs phone">
    <svg width="56" height="56" viewBox="0 0 56 56" aria-hidden="true">
      <rect x="12" y="30" width="32" height="22" rx="4" fill="#7a2e18"/>
      <circle cx="28" cy="41" r="7" fill="#d8cdb8"/>
      <path d="M6 14 Q28 2 50 14 L46 22 Q28 14 10 22 Z" fill="#5a2010"/>
      <rect x="24" y="20" width="8" height="12" fill="#5a2010"/>
    </svg>
    <span class="phone-number">08 5550 1927</span>
  </div>
  <div class="abs slider-frame">
    <div class="abs slide-photo" role="img" aria-label="Photograph looking up into white gum tree branches against blue sky"></div>
  </div>
  <div class="abs slide-caption">
    <div class="abs caption-title">LOREM IPSUM IS SIMPLY DUMMY TEXT</div>
    <div class="abs caption-text">LOREM IPSUM IS SIMPLY DUMMY TEXT OF THE PRINTING AND TYPESETTING INDUSTRY.</div>
  </div>
  <div class="abs slide-dots"><span></span><span></span><span></span><span></span></div>
</header>

<nav class="abs main-nav">
  <div class="abs nav-item active" style="left:159px;width:123px"><span class="nav-title">HOME</span><span class="nav-sub">Welcome to our Company</span></div>
  <div class="abs nav-item" style="left:296px"><span class="nav-title">ABOUT US</span><span class="nav-sub">Know about our brand</span></div>
  <div class="abs nav-item" style="left:418px"><span class="nav-title">OUR SERVICES</span><span class="nav-sub">Claint satistified our services</span></div>
  <div class="abs nav-item" style="left:555px"><span class="nav-title">OUR WORK</span><span class="nav-sub">Do for Latest technology</span></div>
  <div class="abs nav-item" style="left:684px"><span class="nav-title">GET A QUOTE</span><span class="nav-sub">Quote for Free</span></div>
  <div class="abs nav-item" style="left:805px"><span class="nav-title">CONTACT US</span><span class="nav-sub">24 hours online</span></div>
</nav>

<main>
  <h1 class="abs welcome-title">WELCOME TO MCCW</h1>
  <h2 class="abs welcome-tag">MAPLE CREST CANOPY WORKS</h2>
  <div class="abs welcome-divider"></div>
  <p class="abs welcome-text">Lorem Ipsum is simply dummy text of the printing and typesetting industry. Lorem Ipsum has been the industry's standard dummy text ever since the 1500s, when an unknown printer took a galley of type and scrambled it to make a type specimen book. It has survived not only five centuries, but also the leap into electronic typesetting, remaining essentially unchanged. It was popularised in the 1960s with the release of Letraset sheets containing Lorem Ipsum passages.</p>
  <div class="abs rule" style="top:604px"></div>

  <div class="abs card highlight" style="left:159px">
    <h3>DOMESTIC</h3>
    <svg width="62" height="52" viewBox="0 0 62 52" aria-hidden="true"><path d="M31 2 L60 28 L52 28 L52 50 L10 50 L10 28 L2 28 Z" fill="#4a2204"/><rect x="26" y="34" width="10" height="16" fill="#7a3d07"/></svg>
    <p>Lorem Ipsum is simply dummy text of the printing and typesetting industry. Lorem Ipsum has been the industry's.</p>
  </div>
  <div class="abs card" style="left:350px">
    <h3>COMMERCIAL</h3>
    <svg width="62" height="52" viewBox="0 0 62 52" aria-hidden="true"><rect x="22" y="4" width="18" height="16" fill="#1e2412"/><path d="M8 12 L16 12 L16 34 L26 42 L26 50 L16 50 L8 38 Z M54 12 L46 12 L46 34 L36 42 L36 50 L46 50 L54 38 Z" fill="#1e2412"/></svg>
    <p>Lorem Ipsum is simply dummy text of the printing and typesetting industry. Lorem Ipsum has been the industry's.</p>
  </div>
  <div class="abs card" style="left:540px">
    <h3>GOVERNMENT</h3>
    <svg width="62" height="52" viewBox="0 0 62 52" aria-hidden="true"><path d="M31 2 L58 14 L4 14 Z" fill="#1e2412"/><rect x="6" y="16" width="50" height="4" fill="#1e2412"/><rect x="10" y="22" width="6" height="20" fill="#1e2412"/><rect x="22" y="22" width="6" height="20" fill="#1e2412"/><rect x="34" y="22" width="6" height="20" fill="#1e2412"/><rect x="46" y="22" width="6" height="20" fill="#1e2412"/><rect x="4" y="44" width="54" height="6" fill="#1e2412"/></svg>
    <p>Lorem Ipsum is simply dummy text of the printing and typesetting industry. Lorem Ipsum has been the industry's.</p>
  </div>
  <div class="abs card" style="left:730px">
    <h3>NON PROFIT</h3>
    <svg width="62" height="52" viewBox="0 0 62 52" aria-hidden="true"><circle cx="31" cy="26" r="19" fill="none" stroke="#1e2412" stroke-width="7"/><line x1="20" y1="37" x2="42" y2="15" stroke="#1e2412" stroke-width="7"/></svg>
    <p>Lorem Ipsum is simply dummy text of the printing and typesetting industry. Lorem Ipsum has been the industry's.</p>
  </div>

  <div class="abs rule" style="top:820px"></div>

  <h2 class="abs section-title" style="left:158px">SERVICES</h2>
  <ul class="abs services-list">
    <li>Lorem Ipsum is simply</li>
    <li>Lorem Ipsum is simply is simply</li>
    <li>Lorem Ipsum simply</li>
    <li>Lorem Ipsum is simply</li>
    <li>Lorem Ipsum is simply Ipsum</li>
  </ul>

  <h2 class="abs section-title" style="left:387px">RECENT WORKS</h2>
  <div class="abs carousel-arrow" style="left:871px"></div>
  <div class="abs carousel-arrow" style="left:888px"></div>

  <div class="abs thumb" style="left:388px;background:linear-gradient(180deg,#1f3a6a,#0e1a2e)" role="img" aria-label="Photograph of a tree silhouette at dusk">
    <div class="abs thumb-overlay">
      <svg width="26" height="22" viewBox="0 0 26 22" aria-hidden="true"><circle cx="10" cy="9" r="6" fill="none" stroke="#fff" stroke-width="2"/><line x1="14" y1="13" x2="22" y2="19" stroke="#fff" stroke-width="3"/></svg>
      <div>Lorem Ipsum is simply dummy<br>text of the printing.</div>
    </div>
  </div>
  <div class="abs thumb" style="left:568px;background:linear-gradient(180deg,#7fa04a,#8a6a44 60%,#6d8a3a)" role="img" aria-label="Photograph of a broken tree stump on grass"></div>
  <div class="abs thumb" style="left:746px;background:linear-gradient(180deg,#a89a2c,#5e6e22 60%,#4a4a3a)" role="img" aria-label="Photograph of autumn trees along a street"></div>

  <p class="abs works-text">Lorem Ipsum is simply dummy text of the printing and typesetting industry. Lorem Ipsum has been the industry's standard dummy text ever since the 1500s, when an unknown printer took a galley of type and scrambled.</p>
</main>

<div class="abs treeline" role="img" aria-label="Dark silhouette of a forest treeline"></div>

<footer class="abs site-footer">
  <div class="abs footer-links"><span>Home</span><span>About Us</span><span>Our Services</span><span>Our Work</span><span>Get a Quote</span><span>Contact Us</span></div>
  <div class="abs copyright">Copyright © 2013. <b>MCCW</b> - All Rights Reserved | Privacy</div>
  <div class="abs social-label">Connect to<br>Our Social network :</div>
  <div class="abs social" style="left:835px"></div>
  <div class="abs social" style="left:858px;background:#4fa7c9"></div>
  <div class="abs social" style="left:882px;background:#3f7fb0"></div>
</footer>

</body>
</html>
```